Interval Timer App

Need to have design for the attached wireframe. Similar app can be found here: https://shop.lumaverse.net/store/apps/details?id=cc.quillfern.pulseclock

```html
<!DOCTYPE html>
<html lang="en">
<head>
<meta charset="utf-8">
<title>Interval Timer – Settings</title>
<link rel="stylesheet" href="https://fonts.googleapis.com/css2?family=Montserrat:wght@400;500;600&display=swap">
<style>
  :root {
    --screen-bg: #ffffff;
    --ink: #2b2d33;
    --ink-soft: #5c5f66;
    --ink-faint: #b4b6bb;
    --brand: #2f72c4;
    --brand-light: #3d86d8;
    --card-border: #e3e4e7;
    --scrim: rgba(70, 74, 82, 0.32);
    --divider: #e6e7ea;
  }
  * { box-sizing: border-box; margin: 0; padding: 0; }
  html, body { width: 675px; height: 1200px; overflow: hidden; }
  body { font-family: "Montserrat", sans-serif; background: var(--screen-bg); color: var(--ink); position: relative; }

  .settings { position: absolute; inset: 0; }
  .section-title { position: absolute; left: 0; width: 675px; text-align: center; font-weight: 500; color: var(--ink); }
  .section-title.sets { top: 86px; font-size: 36px; }
  .section-title.work { top: 272px; font-size: 40px; }
  .section-title.rest { top: 628px; font-size: 40px; }

  .stepper { position: absolute; top: 170px; left: 0; width: 675px; display: flex; justify-content: center; align-items: center; gap: 70px; }
  .stepper-btn { width: 68px; height: 40px; border-radius: 20px; background: var(--brand); display: flex; align-items: center; justify-content: center; }
  .stepper-value { font-size: 38px; font-weight: 400; width: 30px; text-align: center; }

  .picker-card { position: absolute; left: 81px; width: 515px; border: 2px solid var(--card-border); border-radius: 10px; overflow: hidden; background: var(--screen-bg); }
  .picker-card.work { top: 335px; height: 260px; }
  .picker-card.rest { top: 692px; height: 300px; }
  .picker-label { position: absolute; left: 0; width: 100%; text-align: center; font-size: 24px; color: var(--ink-soft); }
  .picker-row { position: absolute; left: 0; width: 100%; display: flex; justify-content: center; }
  .picker-row span { width: 50px; height: 62px; line-height: 62px; text-align: center; font-size: 31px; color: var(--ink); }
  .picker-row span.faint { color: var(--ink-faint); }
  .picker-row span.selected { width: 62px; margin: 0 -6px; border-radius: 50%; background: var(--brand); color: #fff; }

  .scrim { position: absolute; inset: 0; background: var(--scrim); }

  .options-sheet { position: absolute; left: 0; top: 846px; width: 675px; height: 354px; background: #fff; border-radius: 22px 22px 0 0; }
  .mode-row { position: absolute; top: 0; left: 0; width: 100%; height: 88px; display: flex; align-items: center; padding: 0 38px 0 30px; border-bottom: 2px solid var(--divider); }
  .mode-row .mode-label { margin-left: 28px; font-size: 25px; font-weight: 500; flex: 1; }
  .toggle { width: 74px; height: 34px; border-radius: 17px; background: #f1f2f4; border: 2px solid #e1e2e5; position: relative; }
  .toggle::after { content: ""; position: absolute; right: 6px; top: 6px; width: 18px; height: 18px; border-radius: 50%; background: var(--brand-light); }
  .quick-actions { position: absolute; top: 118px; left: 0; width: 100%; }
  .action { position: absolute; width: 180px; text-align: center; }
  .action svg { display: block; margin: 0 auto; }
  .action .action-label { margin-top: 14px; font-size: 22px; font-weight: 500; color: var(--ink); }
  .action.sound { left: 40px; }
  .action.vibration { left: 247px; }
  .action.feedback { left: 450px; }
</style>
</head>
<body>
  <main class="settings">
    <h2 class="section-title sets">Sets</h2>
    <div class="stepper">
      <div class="stepper-btn"><svg width="20" height="4"><rect width="20" height="4" rx="2" fill="#fff"/></svg></div>
      <div class="stepper-value">3</div>
      <div class="stepper-btn"><svg width="22" height="22"><rect y="9" width="22" height="4" rx="2" fill="#fff"/><rect x="9" width="4" height="22" rx="2" fill="#fff"/></svg></div>
    </div>

    <h2 class="section-title work">Work Interval</h2>
    <section class="picker-card work">
      <div class="picker-label" style="top:20px">Minutes</div>
      <div class="picker-row" style="top:58px">
        <span class="faint">58</span><span>59</span><span>1</span><span>2</span><span class="selected">3</span><span>4</span><span>5</span><span>6</span><span class="faint">7</span>
      </div>
      <div class="picker-label" style="top:140px">Seconds</div>
      <div class="picker-row" style="top:186px">
        <span class="faint">11</span><span>12</span><span>13</span><span>14</span><span class="selected">15</span><span>16</span><span>17</span><span class="faint">18</span><span class="faint">19</span>
      </div>
    </section>

    <h2 class="section-title rest">Rest Interval</h2>
    <section class="picker-card rest">
      <div class="picker-label" style="top:8px">Minutes</div>
      <div class="picker-row" style="top:58px">
        <span class="faint">57</span><span>58</span><span>59</span><span class="selected">1</span><span>2</span><span>3</span><span>4</span><span class="faint">5</span>
      </div>
      <div class="picker-label" style="top:134px">Seconds</div>
    </section>
  </main>

  <div class="scrim"></div>

  <aside class="options-sheet">
    <div class="mode-row">
      <svg width="46" height="46" viewBox="0 0 46 46" fill="none" stroke="#3d86d8" stroke-width="2.5" stroke-linecap="round">
        <circle cx="25" cy="26" r="15"/><path d="M21 6h8M25 6v5M25 26l6-6M36 13l3-3"/><path d="M3 20h7M5 27h5M3 34h7"/>
      </svg>
      <span class="mode-label">Free time mode</span>
      <div class="toggle"></div>
    </div>
    <div class="quick-actions">
      <div class="action sound">
        <svg width="46" height="44" viewBox="0 0 46 44" fill="none" stroke="#3d86d8" stroke-width="2.5" stroke-linejoin="round" stroke-linecap="round">
          <path d="M5 16h8l11-9v30l-11-9H5z"/><path d="M30 16a8 8 0 0 1 0 12M34 11a14 14 0 0 1 0 22"/>
        </svg>
        <div class="action-label">Sound</div>
      </div>
      <div class="action vibration">
        <svg width="52" height="52" viewBox="0 0 52 52" fill="none" stroke="#3d86d8" stroke-width="2.5" stroke-linejoin="round" stroke-linecap="round">
          <rect x="15" y="9" width="22" height="34" rx="3" transform="rotate(-35 26 26)"/><path d="M6 18l-2 5M9 12l-5 10M43 34l5-10M46 40l2-5"/>
        </svg>
        <div class="action-label">Vibration</div>
      </div>
      <div class="action feedback">
        <svg width="50" height="50" viewBox="0 0 50 50" fill="none" stroke="#3d86d8" stroke-width="2.5" stroke-linejoin="round" stroke-linecap="round">
          <path d="M6 6h38v28H30l-5 9-5-9H6z"/><path d="M25 29l-7-7a4.5 4.5 0 0 1 7-5.5 4.5 4.5 0 0 1 7 5.5z"/>
        </svg>
        <div class="action-label">Feedback</div>
      </div>
    </div>
  </aside>
</body>
</html>
```